Exciting opportunity to create logo and a label for our natural health brand.

About us

We are a customer centric health supplement brand who believes in natural medicine and high quality ingredients. We take a holistic approach to healthcare, with an eastern philosophy. We believe in being partners with our customers in their health care journey and are invested in their well being.

Our brand philosophy and values are attached (see Vorna philosophy.png). Our personality traits are:

- Natural
- Fresh
- Modern
- Balanced (in a holistic sense)

Task breakdown

1. Design a fresh feeling logo for us
- We want it to represent our values and high quality ingredients. We would like the quality of the product to be reflected in the branding and have a high end feel.
- Logo text must include Vorna Health Sciences
- We want the Vorna to be the focus of the logo (see uploaded image Vorna logo example.png)
The logo does not have to follow this layout, but we just want the Vorna to stand out. Feel free to use your creative license on this!

2. Create an attractive label to go on the supplement bottle
- The designs need to be eye catching, give a sense of high end ingredients and natural products and tie in with the logo to give a joined up feel.
- We are selling our products online and need them to really stand out from the competition.
- See examples of labels and packaging we like (1 -7 label design).

The initial label we would like you to design would be for our product Calm Drift. It is a product that assists in the management of Anxiety and stress. The label will appear on the bottle that holds the capsules for this supplement, see uploaded files (Example plain bottles.png). The bottles may be white as the picture shows or dark blue recyclable plastic or dark brown glass . We don't have the exact dimensions of the bottle yet, but I will follow up with these.

The label needs to include the following things:
1. The logo
2. The name of the product
3. The product is to help with the relief of Anxiety and Stress
4. Number of capsules the bottle contains
5. The back of the label should have
i) The ingredients
ii) Dosage
iii) Directions of use

Please use placeholder text where needed.

We look forward to seeing your design. Thank you.

```html
<!DOCTYPE html>
<html lang="en">
<head>
<meta charset="utf-8">
<title>Vorna Health Science — Calm Drift Label</title>
<link rel="stylesheet" href="https://fonts.googleapis.com/css2?family=Barlow:wght@400;500;600;700&display=swap">
<style>
  :root {
    --backdrop: #eac5e0;
    --label-white: #ffffff;
    --blush: #f7cbeb;
    --blush-deep: #f4bfe4;
    --ink: #1f1f1f;
    --slate: #5a5a5a;
    --stone: #6d6d6d;
    --botanical: #e4e6e6;
    --divider-shade: #d9d9d9;
  }
  * { box-sizing: border-box; margin: 0; padding: 0; }
  html, body {
    width: 1200px;
    height: 750px;
    overflow: hidden;
    background: var(--backdrop);
    font-family: "Barlow", Arial, sans-serif;
  }
  .canvas {
    position: relative;
    width: 1200px;
    height: 750px;
  }
  .label {
    position: absolute;
    left: 370px;
    top: 95px;
    width: 460px;
    height: 560px;
    background: var(--label-white);
    overflow: hidden;
  }
  .label-bands {
    position: absolute;
    inset: 0;
    width: 460px;
    height: 560px;
  }
  .botanical-area {
    position: absolute;
    left: 210px;
    top: 60px;
    width: 250px;
    height: 450px;
    border-radius: 120px 0 0 60px;
    background: radial-gradient(ellipse at 60% 40%, var(--botanical) 0%, rgba(228,230,230,0.55) 45%, rgba(255,255,255,0) 75%);
  }
  .brand {
    position: absolute;
    left: 0;
    right: 0;
    top: 140px;
    text-align: center;
  }
  .brand-name {
    display: block;
    font-weight: 500;
    font-size: 96px;
    line-height: 1;
    color: var(--blush);
    letter-spacing: 0.01em;
  }
  .brand-descriptor {
    display: block;
    margin-top: 8px;
    font-weight: 700;
    font-size: 12px;
    letter-spacing: 0.75em;
    padding-left: 0.75em;
    color: var(--ink);
  }
  .product-band {
    position: absolute;
    left: 0;
    right: 0;
    top: 318px;
    height: 96px;
    background: var(--label-white);
    border-top: 2px solid var(--divider-shade);
    border-bottom: 2px solid var(--divider-shade);
    box-shadow: 0 6px 8px -6px rgba(0,0,0,0.18), 0 -6px 8px -6px rgba(0,0,0,0.12);
    text-align: center;
    padding-top: 18px;
  }
  .product-name {
    font-weight: 600;
    font-size: 34px;
    line-height: 1;
    color: var(--blush-deep);
  }
  .product-claim {
    margin-top: 6px;
    font-weight: 500;
    font-size: 17px;
    color: var(--slate);
    letter-spacing: 0.02em;
  }
  .capsule-count {
    position: absolute;
    left: 0;
    right: 0;
    top: 440px;
    text-align: center;
    color: var(--stone);
  }
  .capsule-number {
    display: block;
    font-weight: 700;
    font-size: 32px;
    line-height: 1;
  }
  .capsule-unit {
    display: block;
    font-weight: 500;
    font-size: 22px;
    letter-spacing: 0.12em;
    line-height: 1.1;
  }
</style>
</head>
<body>
  <main class="canvas">
    <section class="label">
      <div class="botanical-area" role="img" aria-label="Fine grey line illustration of flowering botanical stems"></div>
      <svg class="label-bands" viewBox="0 0 460 560" aria-hidden="true">
        <path d="M0,0 H460 V46 C320,26 160,20 0,24 Z" fill="var(--blush)"/>
        <path d="M0,526 C150,548 300,552 460,540 V560 H0 Z" fill="var(--blush)"/>
      </svg>
      <header class="brand">
        <span class="brand-name">Vorna</span>
        <span class="brand-descriptor">HEALTH SCIENCE</span>
      </header>
      <div class="product-band">
        <h1 class="product-name">Calm Drift</h1>
        <p class="product-claim">Reduce stress and anxiety naturally</p>
      </div>
      <p class="capsule-count">
        <span class="capsule-number">60</span>
        <span class="capsule-unit">capsules</span>
      </p>
    </section>
  </main>
</body>
</html>
```